Creative Law Firm Business Card

attached are photos of myself and our office as well as language that I would like to see on the card, likely on the back, although I leave that to the designer. I have also attached copies of both sides of a marketing card that we produced just for ideas. I would like to find a tactful way to get my photo in along with the office. I attached copies of our logo, both normal and inverted.

I listed my name as Tom Halloway to be casual, however, it should probably read Thomas J Halloway

Requirements
Must have
• attached file #8 has content.
• I would like my picture and the office photo on page 1
• The text, with the exception of the firm name "HALLOWAY & PEMBER" and the firm description underneath it "THE BUSINESS AND BANKRUPTCY LAWYERS", should be on the back. The layout and fonts are up to the designer

```html
<!DOCTYPE html>
<html lang="en">
<head>
<meta charset="utf-8">
<title>Halloway &amp; Pember – Business Card</title>
<link rel="stylesheet" href="https://fonts.googleapis.com/css2?family=Cinzel:wght@400;600&family=Open+Sans:wght@400&display=swap">
<style>
  :root {
    --page-bg: #dcdcdc;
    --navy: #1b2f5e;
    --navy-deep: #152650;
    --accent-blue: #6c9ad6;
    --card-white: #ffffff;
    --ink: #1f2f5a;
    --ink-soft: #3d4a6b;
    --sky-top: #1f4fc9;
    --sky-mid: #4f7fe0;
    --stone: #d9c6a6;
    --palm: #3c4a2c;
    --suit: #1a1a1c;
    --skin: #d8a088;
  }
  * { margin: 0; padding: 0; box-sizing: border-box; }
  html, body { width: 1200px; height: 852px; overflow: hidden; }
  body {
    background: var(--page-bg);
    display: flex;
    align-items: center;
    justify-content: center;
    gap: 40px;
  }
  .card {
    position: relative;
    width: 540px;
    height: 309px;
    border-radius: 14px;
    overflow: hidden;
    box-shadow: 0 4px 14px rgba(0,0,0,0.18);
  }

  /* Front */
  .card-front .office-photo {
    position: absolute; inset: 0;
    background:
      linear-gradient(180deg, rgba(0,0,0,0) 55%, rgba(40,50,30,0.35) 100%),
      linear-gradient(115deg, var(--sky-top) 0%, var(--sky-mid) 38%, var(--stone) 62%, #c9b48f 80%, var(--palm) 100%);
  }
  .card-front .firm-name {
    position: absolute;
    top: 34px; left: 0; right: 0;
    text-align: center;
    font-family: 'Cinzel', serif;
    font-weight: 400;
    font-size: 38px;
    letter-spacing: 1px;
    color: var(--card-white);
  }

  /* Back */
  .card-back { background: var(--card-white); }
  .card-back .side-band {
    position: absolute; top: 0; bottom: 0; left: 0;
    width: 56px;
    background: var(--accent-blue);
  }
  .card-back .side-band::before {
    content: ""; position: absolute; top: 0; bottom: 0; left: 0;
    width: 50px;
    background: linear-gradient(180deg, var(--navy) 0%, var(--navy-deep) 100%);
  }
  .brand {
    position: absolute; top: 82px; left: 80px;
    display: flex; align-items: center; gap: 10px;
  }
  .brand-mark { width: 28px; height: 28px; background: var(--navy); flex: none; }
  .brand-name {
    font-family: 'Cinzel', serif;
    font-weight: 600;
    font-size: 17px;
    color: var(--ink);
    white-space: nowrap;
  }
  .brand-rule {
    position: absolute; top: 76px; left: 118px;
    width: 205px; height: 1px;
    background: var(--ink);
  }
  .portrait {
    position: absolute; top: 24px; right: 12px;
    width: 150px; height: 226px;
    background: linear-gradient(180deg, #ffffff 0%, #f2e6df 18%, var(--skin) 34%, #6b6b70 48%, var(--suit) 62%, var(--suit) 100%);
    border-radius: 75px 75px 6px 6px;
  }
  .person {
    position: absolute; top: 180px; left: 86px;
  }
  .person-name {
    font-family: 'Cinzel', serif;
    font-size: 15px;
    color: var(--ink-soft);
    letter-spacing: 0.5px;
    white-space: nowrap;
  }
  .person-title {
    font-family: 'Open Sans', sans-serif;
    font-size: 10px;
    color: var(--ink-soft);
    margin-top: 1px;
  }
  .contacts {
    position: absolute; top: 232px; left: 86px;
    list-style: none;
    font-family: 'Open Sans', sans-serif;
    font-size: 12px;
    color: var(--ink);
  }
  .contacts li { display: flex; align-items: center; gap: 8px; line-height: 18px; }
  .contacts svg { width: 11px; height: 11px; fill: var(--navy); flex: none; }
</style>
</head>
<body>

  <section class="card card-front">
    <div class="office-photo" role="img" aria-label="Photo of the firm's office building with palm trees under a blue sky"></div>
    <div class="firm-name">HALLOWAY &amp; PEMBER</div>
  </section>

  <section class="card card-back">
    <div class="side-band"></div>
    <div class="portrait" role="img" aria-label="Portrait photo of the lawyer in a dark suit and tie"></div>
    <div class="brand-rule"></div>
    <div class="brand">
      <span class="brand-mark"></span>
      <span class="brand-name">HALLOWAY &amp; PEMBER</span>
    </div>
    <div class="person">
      <div class="person-name">THOMAS J HALLOWAY</div>
      <div class="person-title">Lawyer</div>
    </div>
    <ul class="contacts">
      <li>
        <svg viewBox="0 0 24 24" aria-hidden="true"><path d="M6.6 10.8a15.1 15.1 0 0 0 6.6 6.6l2.2-2.2c.3-.3.7-.4 1-.2 1.1.4 2.3.6 3.6.6.6 0 1 .4 1 1V20c0 .6-.4 1-1 1A17 17 0 0 1 3 4c0-.6.4-1 1-1h3.5c.6 0 1 .4 1 1 0 1.3.2 2.5.6 3.6.1.3 0 .7-.2 1z"/></svg>
        555-014-2270
      </li>
      <li>
        <svg viewBox="0 0 24 24" aria-hidden="true"><path d="M2 5h20v14H2zm2 2v.5l8 5 8-5V7l-8 5z"/></svg>
        lawyer@hallowaypember.com
      </li>
      <li>
        <svg viewBox="0 0 24 24" aria-hidden="true"><path d="M12 2a10 10 0 1 0 0 20 10 10 0 0 0 0-20zm6.9 9h-3a15 15 0 0 0-1.2-5.6A8 8 0 0 1 18.9 11zM12 4c.9 1.2 1.7 3.9 1.9 7h-3.8c.2-3.1 1-5.8 1.9-7zM9.3 5.4A15 15 0 0 0 8.1 11h-3a8 8 0 0 1 4.2-5.6zM5.1 13h3a15 15 0 0 0 1.2 5.6A8 8 0 0 1 5.1 13zM12 20c-.9-1.2-1.7-3.9-1.9-7h3.8c-.2 3.1-1 5.8-1.9 7zm2.7-1.4a15 15 0 0 0 1.2-5.6h3a8 8 0 0 1-4.2 5.6z"/></svg>
        www.hallowaypember.com
      </li>
    </ul>
  </section>

</body>
</html>
```